Summer Time Cleaning!

Vent Haven Partners Inc. is a family owned business since 2007, RFBLO certified techs, using the most advanced equipment offered in the field. Would like to attract as many customers as possible to bring in a swarm of work during our slow time.please print on jumbo size post card.

Target Market(s)

Main line area homes worth $500,000+

Industry/Entity Type

Residential

Requirements
Must have
• Would like special on Air duct cleaning: Air Duct Cleaning Special- Full home power air duct cleaning only $300.00 offer expires August 29th. Dryer Vent Cleaning Special- Any dryer vent cleaning services includes a FREE lint alert system!
Nice to have
• Would like bright colors, need the post card to really stand out!

```html
<!DOCTYPE html>
<html lang="en">
<head>
<meta charset="utf-8">
<title>Vent Haven Partners – Summer Cleaning Postcard</title>
<link href="https://fonts.googleapis.com/css2?family=Oswald:wght@500;600;700&display=swap" rel="stylesheet">
<style>
  :root {
    --paper: #ffffff;
    --wall-light: #d6cfc4;
    --wall-mid: #b8ad9f;
    --wall-dark: #8f8576;
    --teal: #45c3d2;
    --yellow: #f7d238;
    --sky: #8fd3f2;
    --ocean: #1e8fd6;
    --deep: #1574c4;
    --orange: #f4a431;
    --line: #c9c9c9;
    --ink: #ffffff;
  }
  html, body { margin: 0; padding: 0; overflow: hidden; background: var(--paper); }
  .postcard {
    position: relative;
    width: 1200px;
    height: 668px;
    background: var(--paper);
    overflow: hidden;
    font-family: "Oswald", "Arial Narrow", sans-serif;
  }
  .front-panel {
    position: absolute;
    left: 0; top: 0;
    width: 813px; height: 587px;
    overflow: hidden;
  }
  .scene-photo {
    position: absolute; inset: 0;
    background: radial-gradient(ellipse at 60% 30%, var(--wall-light) 0%, var(--wall-mid) 60%, var(--wall-dark) 100%);
  }
  .waves { position: absolute; inset: 0; }
  .brand {
    position: absolute;
    left: 36px; top: 52px;
    margin: 0;
    color: var(--teal);
    font-weight: 700;
    font-size: 54px;
    line-height: 1;
    letter-spacing: 1px;
    text-transform: uppercase;
  }
  .fact {
    position: absolute;
    left: 37px; top: 220px;
    margin: 0;
    text-transform: uppercase;
    font-weight: 700;
    line-height: 1.08;
  }
  .fact-lead { display: block; color: var(--ink); font-size: 34px; }
  .fact-claim { display: block; color: var(--yellow); font-size: 33px; }
  .offer {
    position: absolute;
    border-radius: 50%;
    border: 4px solid var(--ink);
    box-sizing: border-box;
    color: var(--ink);
    text-align: center;
    text-transform: uppercase;
    display: flex;
    flex-direction: column;
    justify-content: center;
    align-items: center;
    box-shadow: 0 4px 10px rgba(0,0,0,.25);
    transform: rotate(-8deg);
  }
  .offer-duct {
    left: 27px; top: 357px;
    width: 216px; height: 216px;
    background: var(--ocean);
  }
  .offer-price { font-size: 48px; font-weight: 700; line-height: 1; }
  .offer-detail { font-size: 20px; font-weight: 500; line-height: 1.05; margin-top: 4px; }
  .offer-dryer {
    left: 240px; top: 400px;
    width: 166px; height: 166px;
    background: var(--orange);
  }
  .offer-dryer .offer-detail { font-size: 15px; line-height: 1.1; margin: 0; }
  .stamp-box {
    position: absolute;
    left: 1050px; top: 27px;
    width: 123px; height: 150px;
    border: 1px solid var(--line);
    box-sizing: border-box;
  }
  .address-lines {
    position: absolute;
    left: 852px; top: 411px;
    width: 321px;
    margin: 0; padding: 0;
    list-style: none;
  }
  .address-lines li { height: 44px; border-top: 1px solid var(--line); }
</style>
</head>
<body>
  <div class="postcard">
    <section class="front-panel">
      <div class="scene-photo" role="img" aria-label="Photo of a room wall with a metal vent grille, baseboard and wooden floor"></div>
      <svg class="waves" viewBox="0 0 813 587" preserveAspectRatio="none" aria-hidden="true">
        <path d="M0 378 C160 395 300 455 460 450 C600 446 700 430 813 420 L813 587 L0 587 Z" fill="var(--paper)"/>
        <path d="M0 392 C160 410 300 468 460 463 C600 459 700 443 813 432 L813 587 L0 587 Z" fill="var(--sky)"/>
        <path d="M0 470 C200 500 380 520 560 505 C680 495 760 480 813 470 L813 587 L0 587 Z" fill="var(--ocean)"/>
        <path d="M0 530 C260 555 520 560 813 520 L813 587 L0 587 Z" fill="var(--deep)"/>
      </svg>
      <h1 class="brand">Vent Haven<br>Partners</h1>
      <p class="fact">
        <span class="fact-lead">Did you know:</span>
        <span class="fact-claim">Dirty dryer vents are the No1<br>cause of all household fires?</span>
      </p>
      <div class="offer offer-duct">
        <span class="offer-price">$300.00</span>
        <span class="offer-detail">Full home power<br>air duct cleaning</span>
      </div>
      <div class="offer offer-dryer">
        <span class="offer-detail">Any dryer vent<br>cleaning services<br>includes a free<br>lint alert system!</span>
      </div>
    </section>
    <div class="stamp-box" aria-label="Stamp area"></div>
    <ul class="address-lines" aria-label="Address lines">
      <li></li><li></li><li></li><li></li>
    </ul>
  </div>
</body>
</html>
```